Navoro & Omvar Automotive Repair Shop. Need a new website design.

We specialize in Navoro & Omvar auto repair, but also work on other Asian import vehicles. We have been in business for 7 years and pride ourselves on high quality auto repair that is fixed right the first time. Would like the automotive repair website to incorporate the colors black, red and white if possible and have our logo and some Navoro and Omvar vehicles included in the website.

Target Market(s)

Navoro & Omvar vehicle owners

Industry/Entity Type

Automotive Repair

Coding

Coded - Design and coding required

Number of Pages Required

5+ page

Colors
EB3D1F
EC4F4E
F09395
F8D3D4
FCEDEE

Requirements
Must have
• Home, Services, Contact Us, Schedule appointment, and a gallery tab that I can add shop pictures to when completed.
Nice to have
• Would like to see example pictures of job next to each service listed.
Should not have
• Service not related to auto repair. Ex. auto detailing, towing, car wash

```html
<!DOCTYPE html>
<html lang="en">
<head>
<meta charset="utf-8">
<title>Corvan Automotive</title>
<link href="https://fonts.googleapis.com/css2?family=Roboto+Slab:wght@300;400;500;600;700&display=swap" rel="stylesheet">
<style>
:root{
  --red:#d10000;
  --red-bright:#eb3d1f;
  --black:#0b0b0b;
  --white:#ffffff;
  --ink:#1a1a1a;
  --muted:#555555;
  --pale:#efefef;
  --line:#dddddd;
}
*{margin:0;padding:0;box-sizing:border-box}
html,body{width:1200px;height:3577px;overflow:hidden}
body{position:relative;background:var(--white);font-family:"Roboto Slab",serif;color:var(--ink)}
.abs{position:absolute}
.topbar{left:0;top:0;width:1200px;height:38px;background:var(--black);color:var(--white);font-size:13px;display:flex;justify-content:flex-end;align-items:center;padding-right:113px}
.topbar span{padding:0 24px}
.topbar span+span{border-left:2px solid var(--red)}
.nav{left:0;top:38px;width:1200px;height:72px;background:var(--white);display:flex;align-items:center;padding-left:346px;gap:42px;font-size:15px}
.btn{background:var(--red);color:var(--white);font-size:15px;display:flex;align-items:center;justify-content:center;white-space:nowrap}
.nav .btn{position:absolute;left:861px;top:16px;width:227px;height:42px}
.logo-tab{left:111px;top:0;width:203px;height:206px;background:var(--white);clip-path:polygon(0 0,100% 0,100% 80%,50% 100%,0 80%);z-index:3;display:flex;align-items:center;justify-content:center;padding-bottom:40px}
.brand{font-weight:700;color:var(--red);font-size:24px;display:flex;align-items:center;gap:8px}
.brand i{width:14px;height:14px;background:var(--red);border-radius:50%;display:block}
.hero{left:0;top:110px;width:1200px;height:654px;background:linear-gradient(100deg,#2c2c2c 0%,#4a4a4a 45%,#6b6b6b 70%,#3a3a3a 100%)}
.hero-text{left:112px;top:265px;color:var(--white);width:540px}
.hero-text .h1a{font-size:48px;font-weight:400;line-height:58px}
.hero-text .h1b{font-size:58px;font-weight:700;line-height:68px;margin-top:4px}
.hero-text p{font-size:20px;line-height:28px;margin-top:22px}
.hero-text .btn{width:186px;height:42px;margin-top:38px}
.section-bg{left:0;top:764px;width:1200px;height:1121px;background:linear-gradient(180deg,#f2f2f2 0%,#e6e6e6 40%,#ededed 100%)}
.form{left:111px;top:694px;width:978px;height:316px;background:var(--red);padding:48px 24px 0}
.grid{display:grid;grid-template-columns:repeat(4,217px);column-gap:21px;row-gap:14px}
.field label{display:block;color:var(--white);font-weight:700;font-size:17px;margin-bottom:6px}
.field div{height:36px;background:var(--white);font-size:11px;color:#555;padding:0 14px;display:flex;align-items:center;justify-content:space-between}
.submit{margin:30px auto 0;width:215px;height:38px;border:2px solid var(--white);color:var(--white);display:flex;align-items:center;justify-content:center;font-size:15px}
h2{font-size:40px;font-weight:700;color:var(--ink)}
.about-title{left:113px;top:1088px}
.about-text{left:112px;top:1160px;width:520px;font-size:15px;line-height:27.5px;color:#444}
.cars{left:680px;top:1104px;width:498px;height:285px;background:radial-gradient(ellipse at 50% 55%,#9a9a9a 0%,#cfcfcf 55%,rgba(230,230,230,0) 75%)}
.svc-title{left:111px;top:1480px}
.card{top:1565px;width:307px;height:236px;background:var(--white);border:1px solid var(--line);box-shadow:0 2px 6px rgba(0,0,0,.12);padding:32px 27px}
.card .ic{width:40px;height:36px;background:var(--red);border-radius:4px}
.card h3{font-size:19px;font-weight:500;margin-top:18px}
.card p{font-size:15px;line-height:22px;color:#555;margin-top:10px;font-weight:300}
.arrow{top:1661px;width:40px;height:40px;border-radius:50%;background:var(--black)}
.gal-title{left:0;width:1200px;top:1957px;text-align:center}
.ph{width:307px;background:linear-gradient(135deg,#5c5c5c,#8a8a8a 50%,#3d3d3d)}
.view{left:529px;top:2567px;width:142px;height:42px}
.dark-band{left:0;top:3043px;width:1200px;height:534px;background:var(--black)}
.makes{left:111px;top:2694px;width:978px;height:487px;background:var(--white);box-shadow:0 2px 10px rgba(0,0,0,.15);text-align:center;padding-top:82px}
.makes h2{font-size:38px;line-height:47px;font-weight:600}
.make-grid{display:grid;grid-template-columns:repeat(4,1fr);row-gap:80px;margin-top:48px;padding:0 40px;font-size:24px;font-weight:700;color:var(--black);letter-spacing:1px}
.foot-logo{left:108px;top:3320px;font-size:34px}
.fcol{color:var(--white);font-size:15px}
.fcol h4{font-size:20px;font-weight:500;margin-bottom:20px}
.fcol li{list-style:none;margin-bottom:14px}
.contact li{display:flex;gap:16px;align-items:flex-start;margin-bottom:20px;line-height:21px}
.badge{top:3442px;width:70px;height:70px;border-radius:50%;background:var(--white)}
.rule{left:0;top:3539px;width:1200px;height:1px;background:#666}
.copy{left:0;top:3551px;width:1200px;text-align:center;color:var(--white);font-size:13px}
.ver{left:1134px;top:3556px;color:var(--white);font-size:8px}
</style>
</head>
<body>
<div class="abs topbar"><span>Call: 555.289.0143</span><span>Email: service@corvanauto.example</span><span>Hours of Operation: M-F 8:30-6pm</span></div>
<nav class="abs nav"><span>Home</span><span>About Us</span><span>Services</span><span>Gallery</span><span>Contact Us</span><span class="btn">Schedule An Appointment</span></nav>
<div class="abs logo-tab"><div class="brand"><i></i>CORVAN</div></div>

<div class="abs hero" role="img" aria-label="Mechanic working under a raised vehicle in the repair shop"></div>
<div class="abs hero-text">
  <div class="h1a">Welcome To</div>
  <div class="h1b">Corvan Automotive</div>
  <p>Corvan Automotive is a locally owned and operated auto repair shop in Brookhollow that offers comprehensive car care and services for Navoro &amp; Omvar and all other Asian imports vehicles.</p>
  <div class="btn">Schedule An Appointment</div>
</div>

<div class="abs section-bg" role="img" aria-label="Faded engine bay background"></div>

<form class="abs form">
  <div class="grid">
    <div class="field"><label>Name</label><div>Name</div></div>
    <div class="field"><label>Email Address</label><div>Email Address</div></div>
    <div class="field"><label>Year</label><div>Year<span>▾</span></div></div>
    <div class="field"><label>Message</label><div>Message</div></div>
    <div class="field"><label>Phone</label><div>Phone</div></div>
    <div class="field"><label>Service/Repair</label><div>Choose<span>▾</span></div></div>
    <div class="field"><label>Make</label><div>Make<span>▾</span></div></div>
    <div class="field"><label>Model</label><div>Model<span>▾</span></div></div>
  </div>
  <div class="submit">Submit</div>
</form>

<h2 class="abs about-title">About Us</h2>
<p class="abs about-text">Led by an NMT master certified technician with 20 years experience working for Navoro &amp; Omvar dealerships, our auto shop is your go to facility for everything from factory auto maintenance, including oil changes, fluid services and tune ups, to complex engine repairs, hybrid diagnostic &amp; repair, brake jobs, etc. We have state of the art equipment and tools to ensure that we can properly diagnose and repair your vehicle right the first time. Our work comes with a warranty and we offer a free inspection with every visit. We also offer discounts for Ridello &amp; Zipway drivers.</p>
<div class="abs cars" role="img" aria-label="White Navoro SUV and grey Omvar sedan"></div>

<h2 class="abs svc-title">Our Services</h2>
<svg class="abs arrow" style="left:52px" viewBox="0 0 40 40"><circle cx="20" cy="20" r="20" fill="#0b0b0b"/><path d="M23 12l-8 8 8 8" stroke="#fff" stroke-width="3" fill="none"/></svg>
<div class="abs card" style="left:111px"><div class="ic"></div><h3>Oil Changes</h3><p>Factory grade oil and filters for your Navoro or Omvar, with a free fluid level check on every visit.</p></div>
<div class="abs card" style="left:444px"><div class="ic"></div><h3>Computer Diagnostics</h3><p>Dealer level scan tools pinpoint warning lights and engine faults fast, so the fix is right first time.</p></div>
<div class="abs card" style="left:779px"><div class="ic"></div><h3>Electrical Specialists</h3><p>Batteries, starters, alternators, wiring and hybrid systems tested and repaired by certified techs.</p></div>
<svg class="abs arrow" style="left:1107px" viewBox="0 0 40 40"><circle cx="20" cy="20" r="20" fill="#0b0b0b"/><path d="M17 12l8 8-8 8" stroke="#fff" stroke-width="3" fill="none"/></svg>

<h2 class="abs gal-title">Our Gallery</h2>
<div class="abs ph" style="left:111px;top:2046px;height:235px" role="img" aria-label="Engine block being rebuilt"></div>
<div class="abs ph" style="left:445px;top:2046px;height:235px" role="img" aria-label="Open engine bay during repair"></div>
<div class="abs ph" style="left:780px;top:2046px;height:235px" role="img" aria-label="Technicians under a lifted car"></div>
<div class="abs ph" style="left:111px;top:2310px;height:233px" role="img" aria-label="Silver truck on a lift"></div>
<div class="abs ph" style="left:445px;top:2310px;height:233px" role="img" aria-label="Clutch disc and pressure plate"></div>
<div class="abs ph" style="left:780px;top:2310px;height:233px;background:linear-gradient(135deg,#8a1a1a,#c23a3a 55%,#6a5a4a)" role="img" aria-label="Strut assembly on a workbench"></div>
<div class="abs btn view">View All</div>

<div class="abs dark-band"></div>
<div class="abs makes">
  <h2>Corvan Automotive specializes in Navoro &amp; Omvar<br>auto repair but also service and repair the<br>following makes:</h2>
  <div class="make-grid">
    <span>HARUKAN</span><span>AVENO</span><span>NEXORA</span><span>ILLUMIS</span>
    <span>HANSEO</span><span>KIVO</span><span>MIRASU</span><span>MAZURO</span>
  </div>
</div>

<div class="abs brand foot-logo"><i style="width:20px;height:20px"></i>CORVAN</div>
<div class="abs fcol" style="left:482px;top:3255px"><h4>Products</h4><ul><li>Home</li><li>About Us</li><li>Services</li><li>Gallery</li><li>Contact Us</li></ul></div>
<div class="abs fcol contact" style="left:652px;top:3255px">
  <h4 style="margin-left:31px">Contact Us</h4>
  <ul>
    <li><svg width="14" height="14" viewBox="0 0 24 24"><path fill="#fff" d="M6.6 10.8a15 15 0 006.6 6.6l2.2-2.2a1 1 0 011-.25 11 11 0 003.6.6 1 1 0 011 1V20a1 1 0 01-1 1A17 17 0 013 4a1 1 0 011-1h3.5a1 1 0 011 1 11 11 0 00.6 3.6 1 1 0 01-.25 1z"/></svg>555.513.0172</li>
    <li><svg width="14" height="14" viewBox="0 0 24 24"><path fill="#fff" d="M2 5h20v14H2z M2 5l10 8 10-8" stroke="#0b0b0b" stroke-width="1.5"/></svg>service@corvanauto.example</li>
    <li><svg width="14" height="16" viewBox="0 0 24 24"><path fill="#fff" d="M12 2a7 7 0 00-7 7c0 5 7 13 7 13s7-8 7-13a7 7 0 00-7-7zm0 9.5A2.5 2.5 0 1112 6.5a2.5 2.5 0 010 5z"/></svg>412 Harbor Point Circle #5 Brook-<br>hollow, TX 75000</li>
  </ul>
</div>
<div class="abs fcol" style="left:990px;top:3255px"><h4>Follow Us</h4><ul><li style="margin-bottom:10px">Facelink</li><li style="margin-bottom:10px">WorkNet</li><li>Snapgram</li></ul></div>
<div class="abs badge" style="left:731px"></div>
<div class="abs badge" style="left:825px"></div>
<div class="abs badge" style="left:920px"></div>
<div class="abs badge" style="left:1015px"></div>
<div class="abs rule"></div>
<div class="abs copy">© 2024 Corvan Automotive LLC</div>
<div class="abs ver">v2</div>
</body>
</html>
```